Verdana Crest New Website - Online Learning and Education

New Wordpress website for an online learning site that has courses, worksheets, quizzes, etc.
Updates

We would like something similar to this website: https://hallowaybridgeinstitute.example/mediation-skills-course/. But continue with the content of our current website: http://verdanacrestlearninghub.example

We would like something similar to this site: https://hallowaybridgeinstitute.example/mediation-skills-course/

Coding

Coded - Design and coding required

```html
<!DOCTYPE html>
<html lang="en">
<head>
<meta charset="utf-8">
<title>Verdana Crest – Learn Anywhere Any Time</title>
<link href="https://fonts.googleapis.com/css2?family=Montserrat:wght@400;500;600;700;800&family=Open+Sans:wght@400;600;700&display=swap" rel="stylesheet">
<style>
:root{
  --navy:#163a70;
  --navy-dark:#1a3566;
  --red:#b5121b;
  --text:#555b66;
  --muted:#6a6f78;
  --pale:#eef3fb;
  --line:#d9dde3;
  --white:#ffffff;
}
*{margin:0;padding:0;box-sizing:border-box}
html,body{width:1200px;height:4065px;overflow:hidden;background:var(--white)}
body{position:relative;font-family:'Open Sans',sans-serif;color:var(--text)}
.abs{position:absolute}
.center-text{text-align:center;left:0;width:1200px}
h1,h2,h3,h4{font-family:'Montserrat',sans-serif}

/* top bar */
.topbar{position:absolute;left:0;top:0;width:1200px;height:32px;background:var(--navy-dark);color:#fff;font-size:14px;font-weight:600}
.topbar .contact{position:absolute;left:110px;top:6px;display:flex;gap:10px;align-items:center}
.topbar svg{vertical-align:-2px;margin-right:6px}
.signin{position:absolute;right:0;top:0;width:222px;height:32px;background:var(--red);clip-path:polygon(14px 0,100% 0,100% 100%,0 100%);color:#fff;font-size:13px;font-weight:700;padding:7px 0 0 46px;letter-spacing:.3px}

/* nav */
.nav{position:absolute;left:0;top:32px;width:1200px;height:99px;background:#fff}
.brand{position:absolute;left:110px;top:28px;display:flex;align-items:center;gap:12px;font-family:'Montserrat',sans-serif;font-weight:600;font-size:33px;color:var(--navy);letter-spacing:.5px}
.brand .mark{width:36px;height:36px;border-radius:50%;background:var(--navy)}
.menu{position:absolute;left:476px;top:39px;display:flex;gap:28px;font-family:'Montserrat',sans-serif;font-size:16px;font-weight:500;color:#222}
.menu .active{color:var(--red);position:relative}
.menu .active::after{content:"";position:absolute;left:50%;top:30px;transform:translateX(-50%);border-left:13px solid transparent;border-right:13px solid transparent;border-bottom:11px solid var(--red)}

/* hero */
.hero{position:absolute;left:0;top:131px;width:1200px;height:615px;overflow:hidden}
.hero .photo{position:absolute;inset:0;background:linear-gradient(100deg,#2d4a1f 0%,#46682a 30%,#6f8f3c 55%,#c9a451 72%,#4e6a2e 88%,#3a5424 100%)}
.hero .shade{position:absolute;inset:0;background:linear-gradient(90deg,rgba(0,0,0,.35),rgba(0,0,0,0) 55%)}
.hero .kicker{position:absolute;left:110px;top:112px;color:#fff;font-family:'Montserrat',sans-serif;font-weight:500;font-size:48px}
.hero h1{position:absolute;left:110px;top:178px;color:#fff;font-weight:800;font-size:76px;line-height:88px;letter-spacing:1px}
.btn-outline{position:absolute;border:2px solid #fff;border-radius:30px;color:#fff;font-family:'Open Sans',sans-serif;font-weight:700;font-size:16px;text-align:center;letter-spacing:.3px}
.hero .btn-outline{left:110px;top:380px;width:251px;height:60px;line-height:56px}
.slide-arrow{position:absolute;top:372px;width:38px;height:56px;background:rgba(0,0,0,.55);display:flex;align-items:center;justify-content:center}

/* buttons */
.btn-red{position:absolute;background:var(--red);color:#fff;border-radius:30px;font-weight:700;font-size:16px;text-align:center;letter-spacing:.3px}

/* section titles */
.section-title{position:absolute;left:0;width:1200px;text-align:center;color:var(--navy);font-weight:700;font-size:45px;letter-spacing:1px}
.lead{position:absolute;left:0;width:1200px;text-align:center;font-size:15px;line-height:29px;color:var(--muted)}

/* features */
.feature{position:absolute;width:320px;text-align:center}
.feature svg{display:block;margin:0 auto}
.feature h3{color:var(--red);font-weight:500;font-size:25px;margin-top:20px}
.feature p{font-size:14px;line-height:27.5px;color:var(--muted);margin-top:16px}

/* categories */
.categories{position:absolute;left:0;top:1427px;width:1200px;height:754px;background:var(--pale)}
.tabs{position:absolute;left:0;width:1200px;top:158px;display:flex;justify-content:center;gap:40px;font-family:'Montserrat',sans-serif;font-weight:500;font-size:21px;color:#444}
.tabs .on{color:var(--red)}
.card{position:absolute;top:233px;width:231px;height:300px;background:#fff;box-shadow:0 2px 8px rgba(20,40,80,.12)}
.card .pic{height:165px}
.card h4{font-weight:500;font-size:19px;line-height:29px;color:#222;margin:18px 16px 0}
.card .meta{margin:12px 16px 0;font-size:13px;color:#444;display:flex;align-items:center;gap:5px}
.circle-arrow{position:absolute;width:48px;height:48px;border:2px solid #9aa2ad;border-radius:50%;display:flex;align-items:center;justify-content:center;background:#fff}

/* why choose */
.why-item{position:absolute;width:260px}
.why-item h4{font-weight:500;font-size:21px;color:#222}
.why-item p{font-size:13.5px;line-height:24px;color:var(--muted);margin-top:9px}
.why-left{text-align:right;left:55px}
.why-right{left:885px}
.why-icon{position:absolute;width:94px;height:94px;border:2px solid #d2d6dc;border-radius:50%;background:#fff;display:flex;align-items:center;justify-content:center}
.emblem{position:absolute;left:462px;top:2448px;width:276px;height:276px;border-radius:50%;background:var(--navy)}

/* cta band */
.cta{position:absolute;left:0;top:2946px;width:1200px;height:402px}
.cta h2{position:absolute;left:569px;top:78px;color:#fff;font-weight:700;font-size:44px;letter-spacing:1px}
.cta p{position:absolute;left:569px;top:150px;width:540px;color:#fff;font-size:14.5px;line-height:27px}
.cta .btn-outline{left:569px;top:266px;width:166px;height:57px;line-height:53px}

/* contact */
.sub-title{position:absolute;font-family:'Montserrat',sans-serif;font-weight:500;font-size:22px;color:#222}
.field{position:absolute;border:1px solid #9aa0a8;border-radius:4px;font-size:13px;color:#555;padding:12px 16px;background:#fff}
.info-row{position:absolute;left:777px;display:flex;align-items:flex-start;gap:16px;font-size:13.5px;line-height:24px;color:#444}
.info-icon{width:34px;height:34px;border-radius:50%;border:1px solid #c8ccd2;display:flex;align-items:center;justify-content:center;flex-shrink:0}
.social{position:absolute;top:3883px;width:36px;height:36px;border-radius:50%;border:1px solid #9aa0a8}
.footer-line{position:absolute;left:110px;top:3961px;width:970px;height:1px;background:var(--line)}
.copyright{position:absolute;left:0;width:1200px;top:4000px;text-align:center;font-size:13px;color:#555}
</style>
</head>
<body>

<!-- top bar -->
<div class="topbar">
  <div class="contact">
    <span><svg width="12" height="12" viewBox="0 0 24 24"><path fill="#fff" d="M6.6 10.8a15 15 0 0 0 6.6 6.6l2.2-2.2a1 1 0 0 1 1-.25 11.4 11.4 0 0 0 3.6.57 1 1 0 0 1 1 1V20a1 1 0 0 1-1 1A17 17 0 0 1 3 4a1 1 0 0 1 1-1h3.5a1 1 0 0 1 1 1c0 1.25.2 2.45.57 3.57a1 1 0 0 1-.25 1z"/></svg>1 800 555 0142</span>
    <span>|</span>
    <span><svg width="14" height="12" viewBox="0 0 24 20"><path fill="#fff" d="M2 2h20v16H2z M2 2l10 8 10-8" stroke="#1a3566" stroke-width="2"/></svg>info@verdanacrest.example</span>
  </div>
  <div class="signin"><svg width="11" height="12" viewBox="0 0 22 24" style="vertical-align:-1px;margin-right:6px"><circle cx="11" cy="6" r="6" fill="#fff"/><path d="M0 24c0-7 5-10 11-10s11 3 11 10z" fill="#fff"/></svg>SIGN IN</div>
</div>

<!-- navigation -->
<header class="nav">
  <div class="brand"><span class="mark"></span>VERDANA CREST</div>
  <nav class="menu">
    <span class="active">Home</span><span>About</span><span>Courses</span><span>Worksheets</span><span>Quizzes</span><span>Blog</span><span>Contact</span>
    <svg width="16" height="16" viewBox="0 0 24 24" style="margin-top:2px"><circle cx="10" cy="10" r="7" fill="none" stroke="#222" stroke-width="3"/><path d="M15 15l7 7" stroke="#222" stroke-width="3"/></svg>
  </nav>
</header>

<!-- hero -->
<section class="hero">
  <div class="photo" role="img" aria-label="Photo of a smiling young woman working on a laptop on a park bench in front of green hedges"></div>
  <div class="shade"></div>
  <div class="kicker">LEARN</div>
  <h1>ANYWHERE<br>ANY TIME</h1>
  <div class="btn-outline">START MY FREE MONTH</div>
  <div class="slide-arrow" style="left:0"><svg width="14" height="22" viewBox="0 0 14 22"><path d="M11 2L3 11l8 9" fill="none" stroke="#fff" stroke-width="2.5"/></svg></div>
  <div class="slide-arrow" style="right:0"><svg width="14" height="22" viewBox="0 0 14 22"><path d="M3 2l8 9-8 9" fill="none" stroke="#fff" stroke-width="2.5"/></svg></div>
</section>

<!-- welcome -->
<h2 class="section-title" style="top:826px">WELCOME TO VERDANA CREST</h2>
<p class="lead" style="top:907px">Nam libero tempore, cum soluta nobis est eligendi optio cumque nihil impedit quo minus id quod maxime<br>placeat facere possimus, omnis voluptas assumenda est, omnis dolor repellendus</p>

<div class="feature" style="left:97px;top:1018px">
  <svg width="66" height="48" viewBox="0 0 66 48"><path d="M33 4L2 17l31 13 31-13z" fill="#b5121b"/><path d="M14 24v12c0 6 38 6 38 0V24L33 32z" fill="#b5121b"/><path d="M60 19v18" stroke="#b5121b" stroke-width="3"/></svg>
  <h3>Courses</h3>
  <p>At vero eos et accusamus et iusto odio ignissimos ducimus qui blanditiis praesentium voluptatum delesamniti atque corr</p>
</div>
<div class="feature" style="left:440px;top:1018px">
  <svg width="56" height="48" viewBox="0 0 56 48"><rect x="6" y="8" width="36" height="36" rx="6" fill="none" stroke="#b5121b" stroke-width="4"/><path d="M20 32l3-9 20-20 6 6-20 20z" fill="#b5121b"/></svg>
  <h3>Worksheets</h3>
  <p>At vero eos et accusamus et iusto odio ignissimos ducimus qui blanditiis praesentium voluptatum delesamniti atque corr</p>
</div>
<div class="feature" style="left:780px;top:1018px">
  <svg width="50" height="48" viewBox="0 0 50 48"><path d="M4 12h12a5 5 0 1 1 10 0h12v12a5 5 0 1 1 0 10v12H26a5 5 0 1 0-10 0H4z" fill="#b5121b"/></svg>
  <h3>Quizzes</h3>
  <p>At vero eos et accusamus et iusto odio ignissimos ducimus qui blanditiis praesentium voluptatum delesamniti atque corr</p>
</div>
<div class="btn-red" style="left:516px;top:1276px;width:168px;height:54px;line-height:54px">GET STARTED</div>

<!-- categories -->
<section class="categories">
  <h2 class="section-title" style="top:80px">EXPLORE ONLINE CATEGORIES</h2>
  <div class="tabs"><span class="on">Courses</span><span>Worksheets</span><span>Quizzes</span></div>

  <div class="card" style="left:110px">
    <div class="pic" role="img" aria-label="Photo of students studying together at a table" style="background:linear-gradient(135deg,#6b5a4a,#b89572,#5a6070)"></div>
    <h4>Temporibus autem<br>quibusm etau</h4>
    <div class="meta"><svg width="12" height="12" viewBox="0 0 24 24"><circle cx="12" cy="12" r="10" fill="none" stroke="#163a70" stroke-width="3"/><path d="M12 6v6l4 2" stroke="#163a70" stroke-width="3" fill="none"/></svg>6h 4m | <svg width="14" height="10" viewBox="0 0 28 18" style="margin-left:4px"><path d="M1 9C6 1 22 1 27 9 22 17 6 17 1 9z" fill="#163a70"/><circle cx="14" cy="9" r="4" fill="#fff"/></svg>3,067,321 Views</div>
  </div>
  <div class="card" style="left:360px">
    <div class="pic" role="img" aria-label="Photo of a hand with a pen over a calculator and papers" style="background:linear-gradient(135deg,#c9d3df,#5f7ea6,#26456f)"></div>
    <h4>Temporibus autem<br>quibusm etau</h4>
    <div class="meta"><svg width="12" height="12" viewBox="0 0 24 24"><circle cx="12" cy="12" r="10" fill="none" stroke="#163a70" stroke-width="3"/><path d="M12 6v6l4 2" stroke="#163a70" stroke-width="3" fill="none"/></svg>6h 4m | <svg width="14" height="10" viewBox="0 0 28 18" style="margin-left:4px"><path d="M1 9C6 1 22 1 27 9 22 17 6 17 1 9z" fill="#163a70"/><circle cx="14" cy="9" r="4" fill="#fff"/></svg>3,067,321 Views</div>
  </div>
  <div class="card" style="left:609px">
    <div class="pic" role="img" aria-label="Photo of a woman working at a computer in an office" style="background:linear-gradient(135deg,#e6e8ea,#a89a8c,#d2d5d9)"></div>
    <h4>Temporibus autem<br>quibusm etau</h4>
    <div class="meta"><svg width="12" height="12" viewBox="0 0 24 24"><circle cx="12" cy="12" r="10" fill="none" stroke="#163a70" stroke-width="3"/><path d="M12 6v6l4 2" stroke="#163a70" stroke-width="3" fill="none"/></svg>6h 4m | <svg width="14" height="10" viewBox="0 0 28 18" style="margin-left:4px"><path d="M1 9C6 1 22 1 27 9 22 17 6 17 1 9z" fill="#163a70"/><circle cx="14" cy="9" r="4" fill="#fff"/></svg>3,067,321 Views</div>
  </div>
  <div class="card" style="left:858px">
    <div class="pic" role="img" aria-label="Photo of a young man with headphones studying at a laptop" style="background:linear-gradient(135deg,#eef0f1,#b8c2c8,#7b8a93)"></div>
    <h4>Temporibus autem<br>quibusm etau</h4>
    <div class="meta"><svg width="12" height="12" viewBox="0 0 24 24"><circle cx="12" cy="12" r="10" fill="none" stroke="#163a70" stroke-width="3"/><path d="M12 6v6l4 2" stroke="#163a70" stroke-width="3" fill="none"/></svg>6h 4m | <svg width="14" height="10" viewBox="0 0 28 18" style="margin-left:4px"><path d="M1 9C6 1 22 1 27 9 22 17 6 17 1 9z" fill="#163a70"/><circle cx="14" cy="9" r="4" fill="#fff"/></svg>3,067,321 Views</div>
  </div>

  <div class="circle-arrow" style="left:31px;top:359px"><svg width="12" height="18" viewBox="0 0 12 18"><path d="M9 2L3 9l6 7" fill="none" stroke="#555" stroke-width="2.5"/></svg></div>
  <div class="circle-arrow" style="left:1121px;top:359px"><svg width="12" height="18" viewBox="0 0 12 18"><path d="M3 2l6 7-6 7" fill="none" stroke="#555" stroke-width="2.5"/></svg></div>

  <div class="btn-red" style="left:476px;top:593px;width:246px;height:54px;line-height:54px">EXPLORE MORE COURSES</div>
</section>

<!-- why choose -->
<h2 class="section-title" style="top:2260px">WHY CHOOSE VERDANA CREST</h2>
<p class="lead" style="top:2341px">Nam libero tempore, cum soluta nobis est eligendi optio cumque nihil impedit quo minus id quod maxime<br>placeat facere possimus, omnis voluptas assumenda est, omnis dolor repellendus</p>

<div class="why-item why-left" style="top:2468px"><h4>Expert Teachers</h4><p>Nam libero tempore, cum souta<br>nobis est eligendi optio cum</p></div>
<div class="why-item why-left" style="top:2631px"><h4>Unlimited Access</h4><p>Nam libero tempore, cum souta<br>nobis est eligendi optio cum</p></div>
<div class="why-item why-right" style="top:2468px"><h4>Learn Anywhere</h4><p>Nam libero tempore, cum souta<br>nobis est eligendi optio cum</p></div>
<div class="why-item why-right" style="top:2631px"><h4>Learn together</h4><p>Nam libero tempore, cum souta<br>nobis est eligendi optio cum</p></div>

<div class="why-icon" style="left:341px;top:2465px"><svg width="32" height="36" viewBox="0 0 22 24"><circle cx="11" cy="6" r="6" fill="#b5121b"/><path d="M0 24c0-7 5-10 11-10s11 3 11 10z" fill="#b5121b"/></svg></div>
<div class="why-icon" style="left:341px;top:2629px"><svg width="48" height="24" viewBox="0 0 48 24"><path d="M24 12C18 2 4 2 4 12s14 10 20 0 20-10 20 0-14 10-20 0z" fill="none" stroke="#b5121b" stroke-width="4.5"/></svg></div>
<div class="why-icon" style="left:764px;top:2465px"><svg width="38" height="38" viewBox="0 0 38 38"><circle cx="19" cy="19" r="17" fill="#b5121b"/><path d="M9 11c5 0 7 3 5 7s3 4 2 9M24 6c-2 4 2 6 5 7s2 6 0 9" stroke="#fff" stroke-width="3" fill="none"/></svg></div>
<div class="why-icon" style="left:764px;top:2629px"><svg width="42" height="34" viewBox="0 0 42 34"><circle cx="21" cy="8" r="6" fill="#b5121b"/><circle cx="8" cy="12" r="4.5" fill="#b5121b"/><circle cx="34" cy="12" r="4.5" fill="#b5121b"/><path d="M10 34c0-10 5-14 11-14s11 4 11 14z" fill="#b5121b"/><path d="M0 30c0-7 3-10 8-10s7 2 7 4L12 30zM42 30c0-7-3-10-8-10s-7 2-7 4l3 6z" fill="#b5121b"/></svg></div>

<div class="emblem" role="img" aria-label="Large brand emblem decoration"></div>

<div class="btn-red" style="left:476px;top:2793px;width:246px;height:54px;line-height:54px">START MY FREE MONTH</div>

<!-- call to action band -->
<section class="cta">
  <svg class="abs" style="left:0;top:0" width="1200" height="402" viewBox="0 0 1200 402">
    <polygon points="390,25 1200,25 1200,377 549,377" fill="#163a70"/>
    <polygon points="371,0 0,0 0,402 528,402" fill="#c9c4bd"/>
  </svg>
  <div class="abs" role="img" aria-label="Photo of a smiling young woman writing in a notebook" style="left:0;top:0;width:528px;height:402px;clip-path:polygon(0 0,371px 0,528px 402px,0 402px);background:linear-gradient(120deg,#3e3a38 0%,#8b7566 35%,#d8cdc2 70%,#eeeae5 100%)"></div>
  <h2>START MY FREE MONTH</h2>
  <p>At vero eos et accusamus et iusto odio dignissimos ducimus qui blanditiispra esentium voluptatum deleniti atque corrupti quos dolores et quas molestias excepturi sint occaecati cu imilique sunti.</p>
  <div class="btn-outline">GET STARTED</div>
</section>

<!-- contact -->
<h2 class="section-title" style="top:3464px">CONTACT US</h2>

<div class="sub-title" style="left:110px;top:3580px">Contact form</div>
<div class="field" style="left:110px;top:3640px;width:298px;height:44px">Name :</div>
<div class="field" style="left:416px;top:3640px;width:298px;height:44px">Phone no :</div>
<div class="field" style="left:110px;top:3701px;width:604px;height:44px">Email :</div>
<div class="field" style="left:110px;top:3763px;width:604px;height:83px">Message :</div>
<div class="btn-red" style="left:609px;top:3865px;width:104px;height:41px;line-height:41px;font-size:14px">SUBMIT</div>

<div class="sub-title" style="left:777px;top:3580px">Contact Information</div>
<div class="info-row" style="top:3628px">
  <div class="info-icon"><svg width="12" height="16" viewBox="0 0 12 16"><path d="M6 0a6 6 0 0 1 6 6c0 4-6 10-6 10S0 10 0 6a6 6 0 0 1 6-6z" fill="#b5121b"/><circle cx="6" cy="6" r="2.2" fill="#fff"/></svg></div>
  <div>410 Harbor Lane, Suite 12<br>Lakeview, Oregon 97630</div>
</div>
<div class="info-row" style="top:3700px">
  <div class="info-icon"><svg width="14" height="14" viewBox="0 0 24 24"><path fill="#b5121b" d="M6.6 10.8a15 15 0 0 0 6.6 6.6l2.2-2.2a1 1 0 0 1 1-.25 11.4 11.4 0 0 0 3.6.57 1 1 0 0 1 1 1V20a1 1 0 0 1-1 1A17 17 0 0 1 3 4a1 1 0 0 1 1-1h3.5a1 1 0 0 1 1 1c0 1.25.2 2.45.57 3.57a1 1 0 0 1-.25 1z"/></svg></div>
  <div style="padding-top:5px">1 800 555 0142</div>
</div>
<div class="info-row" style="top:3760px">
  <div class="info-icon"><svg width="14" height="11" viewBox="0 0 24 18"><rect width="24" height="18" rx="2" fill="#b5121b"/><path d="M1 2l11 8 11-8" stroke="#fff" stroke-width="2" fill="none"/></svg></div>
  <div style="padding-top:5px">info@verdanacrest.example</div>
</div>

<div class="sub-title" style="left:777px;top:3840px">Social Media</div>
<div class="social" style="left:775px"></div>
<div class="social" style="left:821px"></div>
<div class="social" style="left:867px"></div>

<div class="footer-line"></div>
<p class="copyright">Copyright © 2019, Verdana Crest. All rights reserved.</p>
<svg class="abs" style="left:1062px;top:3990px" width="28" height="16" viewBox="0 0 28 16"><path d="M2 14L14 3l12 11" fill="none" stroke="#b8bcc2" stroke-width="3"/></svg>

</body>
</html>
```